Professional & attention grabbing.

A business card design, front and back. I already have a logo I will attach, but I am open to something new as well.
Things to include:
Name:
Title:
Phone:
Email:
Wanting something that is professional but attention grabbing.
Also we do a lot of work using drones on natural gas pipelines (leading the future)if you want to include any of that. I'm open to ideas.
Target Market(s)
Natural gas transmission industry / greenhouse gas mitigation industry
Industry/Entity Type
Business
Colors
Designer to choose colors to be used in the design.
Look and feel
Each slider illustrates characteristics of the customer's brand and the style your logo design should communicate.

```html
<!DOCTYPE html>
<html lang="en">
<head>
<meta charset="utf-8">
<title>Kestrel Inspections – Business Card</title>
<link href="https://fonts.googleapis.com/css2?family=Montserrat:wght@600;700&family=Work+Sans:wght@400;500&display=swap" rel="stylesheet">
<style>
  :root {
    --brand-red: #c12026;
    --ink: #3a3a3c;
    --paper: #ffffff;
    --backdrop: #e4e4e4;
  }
  * { margin: 0; padding: 0; box-sizing: border-box; }
  html, body { width: 1200px; height: 1000px; overflow: hidden; }
  body {
    background: var(--backdrop);
    font-family: "Work Sans", Arial, sans-serif;
    position: relative;
  }
  .card {
    position: absolute;
    left: 224px;
    width: 752px;
    height: 430px;
    overflow: hidden;
    box-shadow: 0 6px 18px rgba(0,0,0,0.18);
  }
  .card--front { top: 40px; background: var(--brand-red); }
  .card--back { top: 530px; background: var(--paper); }

  .wordmark {
    display: flex;
    align-items: center;
    gap: 14px;
    font-family: "Montserrat", Arial, sans-serif;
    font-weight: 700;
    letter-spacing: 0.5px;
  }
  .wordmark__square { display: block; flex: none; }
  .card--front .wordmark {
    position: absolute;
    left: 50%; top: 50%;
    transform: translate(-50%, -50%);
    color: var(--paper);
    font-size: 44px;
  }
  .card--front .wordmark__square { width: 52px; height: 52px; background: var(--paper); }
  .card--back .wordmark {
    position: absolute;
    left: 48px; top: 44px;
    color: var(--ink);
    font-size: 30px;
  }
  .card--back .wordmark__square { width: 36px; height: 36px; background: var(--brand-red); }

  .contact {
    position: absolute;
    left: 48px; top: 208px;
  }
  .contact__name {
    font-family: "Montserrat", Arial, sans-serif;
    font-weight: 700;
    font-size: 24px;
    color: var(--brand-red);
    letter-spacing: 0.5px;
  }
  .contact__title {
    font-family: "Montserrat", Arial, sans-serif;
    font-weight: 600;
    font-size: 15px;
    color: var(--ink);
    margin-top: 2px;
  }
  .contact__list { list-style: none; margin-top: 24px; }
  .contact__item {
    display: flex; align-items: center; gap: 12px;
    font-size: 18px; color: var(--ink);
    margin-bottom: 8px;
  }
  .contact__icon { width: 14px; height: 14px; flex: none; }

  .footer-band { position: absolute; left: 0; bottom: 0; width: 100%; height: 40px; }
</style>
</head>
<body>

  <section class="card card--front" aria-label="Card front">
    <div class="wordmark">
      <span class="wordmark__square"></span>
      <span class="wordmark__name">KESTREL INSPECTIONS</span>
    </div>
  </section>

  <section class="card card--back" aria-label="Card back">
    <div class="wordmark">
      <span class="wordmark__square"></span>
      <span class="wordmark__name">KESTREL INSPECTIONS</span>
    </div>

    <div class="contact">
      <p class="contact__name">DANIEL HARPER</p>
      <p class="contact__title">FOUNDER</p>
      <ul class="contact__list">
        <li class="contact__item">
          <svg class="contact__icon" viewBox="0 0 24 24" aria-hidden="true">
            <path fill="#c12026" d="M6.6 10.8a15.1 15.1 0 0 0 6.6 6.6l2.2-2.2c.3-.3.7-.4 1-.2 1.1.4 2.3.6 3.6.6.6 0 1 .4 1 1V20c0 .6-.4 1-1 1A17 17 0 0 1 3 4c0-.6.4-1 1-1h3.5c.6 0 1 .4 1 1 0 1.3.2 2.5.6 3.6.1.3 0 .7-.2 1z"/>
          </svg>
          <span>000 000 0000</span>
        </li>
        <li class="contact__item">
          <svg class="contact__icon" viewBox="0 0 24 24" aria-hidden="true">
            <rect x="2" y="5" width="20" height="14" fill="#c12026"/>
            <path d="M2 5l10 8 10-8" fill="none" stroke="#fff" stroke-width="2"/>
          </svg>
          <span>hello@kestrelinspect.com</span>
        </li>
      </ul>
    </div>

    <svg class="footer-band" viewBox="0 0 752 40" preserveAspectRatio="none" aria-hidden="true">
      <rect width="752" height="40" fill="#c12026"/>
      <polygon points="552,40 558,40 572,0 566,0" fill="#ffffff"/>
    </svg>
  </section>

</body>
</html>
```